BLS Business Card 2018

Larkmere Chiropractic. We have two locations that we want to advertise on the same card. Brightvale OrthoCore campus address: 3815 Pellham Dr., Suite 240, Flowood, MS 39417. Madison address: 246 Willowmere Dr., Building D., Madison, MS 39284. website: www.drlarkmere-example.com. o:(601)555-0147 f:(601)555-0183

Target Market(s)

Health care decision makers: primary care doctors and mothers

Contact Information for Business Card

I have no idea; up for any suggestions and I'd do much better picking from examples versus describing what I'm looking for. We are in a very high end location and would like the cards to look really sharp.

Requirements
Must have
• My name, Martin R Belvane, D.C.

```html
<!DOCTYPE html>
<html lang="en">
<head>
<meta charset="utf-8">
<title>Larkmere Chiropractic – Business Card</title>
<link href="https://fonts.googleapis.com/css2?family=Merriweather:wght@400;700&display=swap" rel="stylesheet">
<style>
  :root {
    --backdrop: #2b2c2e;
    --card: #1f2023;
    --card-edge: #2a2b2f;
    --band: #0e5f87;
    --accent: #1b7fd0;
    --ink: #f2f2f2;
    --ink-soft: #c9cbd0;
    --emboss: #34363b;
  }
  * { box-sizing: border-box; margin: 0; padding: 0; }
  html, body { width: 799px; height: 1200px; overflow: hidden; }
  body {
    background: var(--backdrop);
    font-family: "Merriweather", Georgia, serif;
    color: var(--ink);
    position: relative;
  }
  .card {
    position: absolute;
    left: 80px;
    width: 640px;
    height: 366px;
    border-radius: 24px;
    background: linear-gradient(150deg, var(--card-edge), var(--card) 60%);
    box-shadow: 0 18px 40px rgba(0,0,0,.45);
    overflow: hidden;
  }
  .card--front { top: 150px; }
  .card--back { top: 700px; }

  /* Front */
  .brand-emboss {
    position: absolute;
    right: 50px; top: 58px;
    display: flex; align-items: center; gap: 14px;
    font-size: 38px; font-weight: 400; letter-spacing: 1px;
    color: var(--emboss);
    white-space: nowrap;
  }
  .brand-emboss .mark {
    width: 22px; height: 22px; border-radius: 50%; background: var(--emboss);
  }
  .band {
    position: absolute; left: 0; right: 0; top: 170px; height: 110px;
    background: var(--band);
  }
  .campus-pill {
    position: absolute; left: 220px; top: 148px;
    width: 210px; height: 42px; border-radius: 21px;
    border: 2px solid var(--ink); background: var(--card);
    display: flex; align-items: center; justify-content: center;
    font-size: 15px; font-weight: 700;
  }
  .address {
    position: absolute; display: flex; gap: 10px;
    font-size: 15px; line-height: 1.45;
    white-space: nowrap;
  }
  .address svg { flex: none; margin-top: 3px; }
  .address--flowood { left: 36px; top: 200px; }
  .address--madison { left: 360px; top: 212px; }
  .band-divider {
    position: absolute; left: 336px; top: 206px; width: 1px; height: 52px;
    background: rgba(255,255,255,.5);
  }
  .web-row {
    position: absolute; left: 0; right: 0; top: 306px;
    display: flex; align-items: center; justify-content: center; gap: 18px;
    font-size: 15px;
  }
  .web-row .rule { width: 60px; height: 2px; background: var(--ink); }

  /* Back */
  .brand {
    position: absolute; left: 40px; top: 138px;
    display: flex; align-items: center; gap: 12px;
    font-size: 26px; font-weight: 400; line-height: 1.2; color: var(--ink);
  }
  .brand .mark { flex: none; width: 18px; height: 18px; border-radius: 50%; background: var(--ink); }
  .back-divider {
    position: absolute; left: 282px; top: 96px; width: 1px; height: 176px;
    background: rgba(255,255,255,.6);
  }
  .person { position: absolute; left: 306px; top: 110px; white-space: nowrap; }
  .person__name { font-size: 21px; font-weight: 700; color: var(--accent); }
  .person__title { font-size: 12px; color: var(--ink-soft); margin-top: 4px; }
  .contact-list { list-style: none; margin-top: 20px; font-size: 12.5px; line-height: 1.75; }
  .contact-list li { display: flex; align-items: center; gap: 10px; }
  .contact-list svg { flex: none; fill: var(--accent); }
</style>
</head>
<body>

<section class="card card--front" aria-label="Card front">
  <div class="brand-emboss"><span class="mark"></span>Larkmere Chiropractic</div>
  <div class="band"></div>
  <div class="campus-pill">OrthoCore Campus</div>
  <div class="address address--flowood">
    <svg width="12" height="16" viewBox="0 0 12 16"><path d="M6 0a6 6 0 0 0-6 6c0 4.5 6 10 6 10s6-5.5 6-10a6 6 0 0 0-6-6zm0 8.5A2.5 2.5 0 1 1 6 3.5a2.5 2.5 0 0 1 0 5z" fill="#fff"/></svg>
    <p>3815 Pellham Dr., Suite 240,<br>Flowood, MS 39417</p>
  </div>
  <div class="band-divider"></div>
  <div class="address address--madison">
    <svg width="12" height="16" viewBox="0 0 12 16"><path d="M6 0a6 6 0 0 0-6 6c0 4.5 6 10 6 10s6-5.5 6-10a6 6 0 0 0-6-6zm0 8.5A2.5 2.5 0 1 1 6 3.5a2.5 2.5 0 0 1 0 5z" fill="#fff"/></svg>
    <p>246 Willowmere Dr., Building D.,<br>Madison, MS 39284</p>
  </div>
  <div class="web-row"><span class="rule"></span><span>www.drlarkmere-example.com</span><span class="rule"></span></div>
</section>

<section class="card card--back" aria-label="Card back">
  <div class="brand"><span class="mark"></span><p>Larkmere<br>Chiropractic</p></div>
  <div class="back-divider"></div>
  <div class="person">
    <p class="person__name">Martin R Belvane, D.C.</p>
    <p class="person__title">Managing Director</p>
    <ul class="contact-list">
      <li><svg width="13" height="13" viewBox="0 0 16 16"><path d="M3 1l3 3-2 2a10 10 0 0 0 6 6l2-2 3 3-2 2C7 15 1 9 1 3z"/></svg>(601)555-0147</li>
      <li><svg width="13" height="13" viewBox="0 0 16 16"><path d="M4 1h8v4H4zM1 6h14v6h-3v3H4v-3H1zm4 4v3h6v-3z"/></svg>(601)555-0183</li>
      <li><svg width="13" height="13" viewBox="0 0 16 16"><path d="M1 3h14v10H1zm1 1v.5l6 4 6-4V4z"/></svg>m.r.belvane@drlarkmere-example.com</li>
      <li><svg width="13" height="13" viewBox="0 0 16 16"><path d="M8 1a7 7 0 1 0 0 14A7 7 0 0 0 8 1zm0 1.5c.8 0 1.8 2 2 4.5H6c.2-2.5 1.2-4.5 2-4.5zM2.6 7a5.5 5.5 0 0 1 2.6-4c-.5 1-.9 2.4-1 4zm0 2h1.6c.1 1.6.5 3 1 4a5.5 5.5 0 0 1-2.6-4zM6 9h4c-.2 2.5-1.2 4.5-2 4.5S6.2 11.5 6 9zm5.8 0h1.6a5.5 5.5 0 0 1-2.6 4c.5-1 .9-2.4 1-4zm0-2c-.1-1.6-.5-3-1-4a5.5 5.5 0 0 1 2.6 4z"/></svg>www.drlarkmere-example.com</li>
    </ul>
  </div>
</section>

</body>
</html>
```